Classy, Elegant, Simple Business Card Design

Looking to have a classy, simple, and elegant design. Want a top notch designed business card. I really like the look of the new torvane credit card. I also like the design I attached. I am trying to reach 21-29 year old females for booking us for there wedding or event. We offer Disc Jockey Service, Photo Booth Rentals, and Uplighting .

Target Market(s)

21-28 year old females

Contact Information for Business Card

Has to have logo, website, email, and phone number

Font styles to use
Other font styles liked:
• open to font choice, modern, clean
Designer to choose
33a6d7
0791cd
0555a3
ffffff

Requirements
Must have
• Has to have logo, website, email, and phone number
Nice to have
• I really like the design of the new torvane credit card. I also included my logo and some designs I like
Should not have
• clutter or too much info

```html
<!DOCTYPE html>
<html lang="en">
<head>
<meta charset="utf-8">
<title>Tidelight Event Group – Business Card</title>
<link href="https://fonts.googleapis.com/css2?family=Jost:wght@300;400;500&family=Roboto+Condensed:wght@400;500&display=swap" rel="stylesheet">
<style>
  :root {
    --stage: #3b3b3d;
    --card-navy: #12305a;
    --card-navy-deep: #0e2a50;
    --accent-sky: #33a6d7;
    --accent-blue: #0791cd;
    --accent-royal: #0555a3;
    --ink-white: #ffffff;
    --ink-muted: #9fb3cc;
  }
  * { box-sizing: border-box; margin: 0; padding: 0; }
  html, body { width: 1200px; height: 1021px; overflow: hidden; }
  body {
    background: var(--stage);
    font-family: "Jost", sans-serif;
    color: var(--ink-white);
    position: relative;
  }
  .card {
    position: absolute;
    left: 300px;
    width: 600px;
    height: 343px;
    background: linear-gradient(135deg, var(--card-navy) 0%, var(--card-navy-deep) 100%);
    box-shadow: 0 14px 30px rgba(0,0,0,0.45);
    overflow: hidden;
  }
  .card--back { top: 100px; }
  .card--front { top: 578px; }

  .card__band {
    position: absolute;
    inset: 0;
  }

  .brand-name {
    font-family: "Jost", sans-serif;
    font-weight: 400;
    color: var(--ink-white);
    text-transform: uppercase;
    line-height: 1.15;
  }

  /* Back: contact side */
  .card--back .brand-name {
    position: absolute;
    left: 42px;
    top: 46px;
    font-size: 26px;
    letter-spacing: 1px;
  }
  .card--back .brand-name span {
    display: block;
    font-size: 12px;
    letter-spacing: 6px;
  }
  .person {
    position: absolute;
    left: 42px;
    top: 150px;
  }
  .person__name {
    font-family: "Roboto Condensed", sans-serif;
    font-weight: 500;
    font-size: 22px;
    color: var(--accent-sky);
    text-transform: uppercase;
    letter-spacing: 0.5px;
  }
  .person__role {
    font-size: 15px;
    margin-top: 2px;
  }
  .address {
    position: absolute;
    left: 42px;
    top: 228px;
    font-size: 14px;
    line-height: 1.45;
  }
  .contact {
    position: absolute;
    right: 40px;
    top: 200px;
    list-style: none;
    font-size: 14px;
    line-height: 1.45;
    text-align: right;
  }
  .contact__icons {
    display: flex;
    justify-content: flex-end;
    gap: 5px;
    margin-bottom: 6px;
  }
  .contact__icons svg { width: 17px; height: 17px; }

  /* Front: brand side */
  .card--front .brand-name {
    position: absolute;
    left: 0;
    right: 0;
    top: 128px;
    text-align: center;
    font-size: 42px;
    letter-spacing: 2px;
  }
  .card--front .brand-name span {
    display: block;
    font-size: 17px;
    letter-spacing: 10px;
    margin-top: 6px;
  }
</style>
</head>
<body>

  <section class="card card--back" aria-label="Business card, contact side">
    <svg class="card__band" viewBox="0 0 600 343" aria-hidden="true">
      <path d="M420 0 C 470 120, 520 230, 600 280 L600 0 Z" fill="var(--accent-royal)" opacity="0.18"/>
    </svg>
    <div class="brand-name">Tidelight<span>Event Group</span></div>
    <div class="person">
      <div class="person__name">Daniel Marsh</div>
      <div class="person__role">Founder</div>
    </div>
    <address class="address" style="font-style:normal">
      48 Harbor Lane, Suite 12<br>
      Coral Bay, Florida, 33010
    </address>
    <ul class="contact">
      <li class="contact__icons">
        <svg viewBox="0 0 20 20" aria-label="Phone"><circle cx="10" cy="10" r="10" fill="var(--accent-blue)"/><path d="M7 5.5l1.6 2.4-1 1.2c.7 1.5 1.8 2.6 3.3 3.3l1.2-1 2.4 1.6-.9 1.8C9.5 14.5 5.5 10.5 5.2 6.4z" fill="#fff"/></svg>
        <svg viewBox="0 0 20 20" aria-label="Email"><circle cx="10" cy="10" r="10" fill="var(--accent-blue)"/><rect x="5" y="6.5" width="10" height="7" fill="none" stroke="#fff" stroke-width="1.2"/><path d="M5 6.5l5 4 5-4" fill="none" stroke="#fff" stroke-width="1.2"/></svg>
        <svg viewBox="0 0 20 20" aria-label="Website"><circle cx="10" cy="10" r="10" fill="var(--accent-blue)"/><circle cx="10" cy="10" r="5" fill="none" stroke="#fff" stroke-width="1.2"/><path d="M5 10h10M10 5c-2.5 3-2.5 7 0 10M10 5c2.5 3 2.5 7 0 10" fill="none" stroke="#fff" stroke-width="1"/></svg>
      </li>
      <li>(555) 210-4486</li>
      <li>daniel@tidelightevents.com</li>
      <li>www.tidelightevents.com</li>
    </ul>
  </section>

  <section class="card card--front" aria-label="Business card, brand side">
    <svg class="card__band" viewBox="0 0 600 343" aria-hidden="true">
      <path d="M0 343 C 160 260, 420 300, 600 200 L600 343 Z" fill="var(--accent-royal)" opacity="0.22"/>
    </svg>
    <div class="brand-name">Tidelight<span>Event Group</span></div>
  </section>

</body>
</html>
```